Investment company needing business card

We are wanting a business card which looks sharp and easy on the eye. We are thinking of having a business card with the logo embossed on it, to really make it stand out. We will only have a small amount of information of the business card, person's name, position, email address and phone number

Contact Information for Business Card

Danielle Frost
Executive Assistant
+64 21 473 5162
danielf@harwickpartners.co.nz

Requirements
Must have
• Embossed logo
Should not have
• Not to be busy

```html
<!DOCTYPE html>
<html lang="en">
<head>
<meta charset="utf-8">
<title>Harwick Partners – Business Card</title>
<link href="https://fonts.googleapis.com/css2?family=Source+Sans+3:wght@400;600;700&display=swap" rel="stylesheet">
<style>
  :root {
    --bg: #1b1b1c;
    --card: #2c2c2e;
    --green: #1fb376;
    --white: #f2f2f2;
    --rule: #4a4a4c;
  }
  * { margin: 0; padding: 0; box-sizing: border-box; }
  html, body { width: 1200px; height: 900px; overflow: hidden; }
  body {
    background: var(--bg);
    font-family: "Source Sans 3", sans-serif;
    position: relative;
  }
  .card {
    position: absolute;
    width: 600px;
    height: 343px;
    background: var(--card);
    border-radius: 18px;
    box-shadow: 0 10px 30px rgba(0,0,0,.45);
  }
  .card--front { left: 150px; top: 90px; }
  .card--back { left: 450px; top: 467px; }

  .brand {
    position: absolute;
    display: flex;
    align-items: center;
    gap: 10px;
    color: var(--green);
    font-weight: 600;
    text-transform: uppercase;
    letter-spacing: 1.5px;
    white-space: nowrap;
  }
  .brand__square { background: var(--green); flex: none; }
  .card--front .brand { left: 40px; top: 158px; font-size: 22px; }
  .card--front .brand__square { width: 22px; height: 22px; }
  .card--back .brand {
    left: 50%; top: 50%;
    transform: translate(-50%, -50%);
    font-size: 38px;
    gap: 16px;
  }
  .card--back .brand__square { width: 38px; height: 38px; }

  .divider {
    position: absolute;
    left: 300px; top: 70px;
    width: 1px; height: 200px;
    background: var(--rule);
  }
  .contact {
    position: absolute;
    left: 326px; top: 96px;
    color: var(--white);
  }
  .contact__name {
    color: var(--green);
    font-weight: 700;
    font-size: 17px;
    text-transform: uppercase;
    letter-spacing: .3px;
  }
  .contact__role { font-size: 15px; margin-bottom: 12px; }
  .contact__list { list-style: none; font-size: 14.5px; }
  .contact__list li { display: flex; align-items: center; gap: 8px; line-height: 22px; }
  .contact__list svg { width: 12px; height: 12px; flex: none; }
</style>
</head>
<body>
  <section class="card card--front">
    <div class="brand"><span class="brand__square"></span>Harwick Partners</div>
    <div class="divider"></div>
    <div class="contact">
      <p class="contact__name">Danielle Frost</p>
      <p class="contact__role">Executive Assistant</p>
      <ul class="contact__list">
        <li>
          <svg viewBox="0 0 24 24" aria-hidden="true"><path fill="#1fb376" d="M6.6 10.8a15.2 15.2 0 0 0 6.6 6.6l2.2-2.2c.3-.3.7-.4 1-.2 1.1.4 2.3.6 3.6.6.6 0 1 .4 1 1V20c0 .6-.4 1-1 1A17 17 0 0 1 3 4c0-.6.4-1 1-1h3.5c.6 0 1 .4 1 1 0 1.3.2 2.5.6 3.6.1.3 0 .7-.2 1z"/></svg>
          +64 21 473 5162
        </li>
        <li>
          <svg viewBox="0 0 24 24" aria-hidden="true"><rect x="2" y="5" width="20" height="14" rx="1" fill="#1fb376"/><path d="M2 6l10 7 10-7" fill="none" stroke="#2c2c2e" stroke-width="2"/></svg>
          danielf@harwickpartners.co.nz
        </li>
        <li>
          <svg viewBox="0 0 24 24" aria-hidden="true"><circle cx="12" cy="12" r="10" fill="#1fb376"/><path d="M2 12h20M12 2c3 3 3 17 0 20M12 2c-3 3-3 17 0 20" fill="none" stroke="#2c2c2e" stroke-width="1.5"/></svg>
          www.harwickpartners.co.nz
        </li>
      </ul>
    </div>
  </section>

  <section class="card card--back">
    <div class="brand"><span class="brand__square"></span>Harwick Partners</div>
  </section>
</body>
</html>
```